Tolvane Inc., a third party debt collection agency needs a Website

Tolvane needs a very basic website (3 basic pages) so that consumers can download forms, potential employees can get required EEO language and see potential jobs, and to show that they are a consumer friendly organization.

I've attached a list of requirements and wishes titled "Tolvane Website Specifications"

Target Market(s)

Consumers that need to repay their government loans; Tolvane will walk through the process to assist them.

Industry/Entity Type

Financial Service

Coding

Coded - Design and coding required

Number of Pages Required

1 page

Font styles to use
Sans Serif

Colors
0355a3

Requirements
Must have
• Tolvane Logo
• See document "Tolvane Website Specifications" for all requirements

```html
<!DOCTYPE html>
<html lang="en">
<head>
<meta charset="utf-8">
<title>Tolvane Inc.</title>
<link href="https://fonts.googleapis.com/css2?family=Open+Sans:wght@400;600;700&family=Roboto:wght@400;500&family=Roboto+Condensed:wght@400;700&display=swap" rel="stylesheet">
<style>
:root{
  --navy:#262a73;
  --crimson:#8b1a1a;
  --ink:#555;
  --light:#f4f4f4;
  --white:#fff;
  --rule:#d6d6d6;
}
*{box-sizing:border-box;margin:0;padding:0}
html,body{width:1200px;height:2230px;overflow:hidden;background:var(--white)}
body{position:relative;font-family:"Open Sans",sans-serif;color:var(--ink)}
.abs{position:absolute}
h1,h2,h3{font-weight:400}

/* hero */
.hero{left:0;top:0;width:1200px;height:656px;overflow:hidden}
.hero-photo{left:0;top:0;width:1200px;height:656px;
  background:linear-gradient(100deg,#eef0f1 0%,#dfe3e6 35%,#cfd6dc 60%,#e9e4df 80%,#f2efec 100%)}
.brand{left:77px;top:92px;font-family:"Roboto Condensed",sans-serif;font-weight:700;font-size:58px;color:var(--crimson);letter-spacing:1px}
.nav{left:544px;top:56px;display:flex;font-family:"Roboto",sans-serif;font-size:19px;color:#222}
.nav a{display:block;height:51px;line-height:51px;padding:0 18px;color:#222;text-decoration:none}
.nav a.current{background:var(--navy);color:var(--white);border-radius:3px;padding:0 21px}
.hero-title{left:79px;top:248px;font-family:"Roboto",sans-serif;font-size:44px;line-height:63px;color:var(--navy)}
.btn-outline{left:77px;top:403px;width:208px;height:51px;border:1.5px solid var(--crimson);color:var(--crimson);
  font-family:"Roboto",sans-serif;font-size:17px;text-align:center;line-height:48px}

/* band */
.band{left:0;top:656px;width:1200px;height:125px;background:var(--navy)}
.band-text{left:79px;top:699px;font-family:"Roboto Condensed",sans-serif;font-size:26.5px;color:var(--white)}
.band-btn{left:779px;top:691px;width:344px;height:51px;background:var(--white);border-radius:3px;color:var(--crimson);
  font-family:"Roboto Condensed",sans-serif;font-size:21px;text-align:center;line-height:51px}

/* welcome */
.section-title{width:1200px;left:0;text-align:center;font-family:"Roboto",sans-serif;font-size:41px;color:var(--navy)}
.section-title em{font-style:normal;color:var(--crimson)}
.welcome-copy{left:150px;top:926px;width:900px;text-align:center;font-size:16px;line-height:25px;color:var(--ink)}

/* credentials */
.credentials{left:0;top:1080px;width:1200px;height:322px;background:var(--light)}
.badge{background:#9aa6b2;border-radius:6px}
.divider{left:601px;top:1123px;width:1px;height:227px;background:var(--rule)}
.cred-title{font-family:"Roboto",sans-serif;font-size:23px;line-height:31px;color:var(--navy)}
.cred-copy{font-size:15.5px;line-height:25px;color:var(--ink)}

/* advice */
.advice-copy{left:210px;top:1497px;width:780px;text-align:center;font-family:"Roboto Condensed",sans-serif;font-size:21px;line-height:31px;color:var(--ink)}
.call-label{left:375px;top:1584px;font-family:"Roboto Condensed",sans-serif;font-size:30px;color:var(--navy)}
.call-icon{left:578px;top:1571px;width:63px;height:63px;border:1.5px solid var(--navy);border-radius:50%}
.call-number{left:652px;top:1582px;font-family:"Roboto Condensed",sans-serif;font-weight:700;font-size:32px;color:var(--crimson)}

/* testimonials */
.testimonials{left:0;top:1685px;width:1200px;height:333px;background:var(--light)}
.avatar{width:125px;height:125px;border-radius:50%;border:1.5px solid var(--navy);background:linear-gradient(160deg,#dfe3e8,#a9b2bd)}
.quote{width:345px;font-size:15.5px;line-height:25px;color:var(--ink)}
.client{font-size:14.5px;font-weight:700;color:var(--crimson)}

/* footer */
.footer{left:0;top:2018px;width:1200px;height:212px;background:var(--crimson);color:var(--white)}
.footer-links{left:79px;top:2049px;display:flex;gap:41px;font-size:17px}
.footer-rule{left:79px;top:2088px;width:1044px;height:1px;background:rgba(255,255,255,.22)}
.footer-heading{left:79px;top:2106px;font-size:21px}
.footer-item{font-size:15.5px;line-height:25px}
.social{top:2053px;width:20px;height:20px;border:2px solid var(--white);border-radius:50%}
</style>
</head>
<body>

<header class="abs hero">
  <div class="abs hero-photo" role="img" aria-label="Photo of a smiling woman working on a laptop in a bright office with colleagues in the background"></div>
  <div class="abs brand">Tolvane, Inc.</div>
  <nav class="abs nav">
    <a class="current">HOME</a>
    <a>CONSUMER INFORMATION</a>
    <a>CAREER</a>
    <a>CONTACT</a>
  </nav>
  <h1 class="abs hero-title">ASSIST CONSUMERS IN<br>RESOLVING THEIR OBLIGATIONS</h1>
  <div class="abs btn-outline">CONTACT US NOW</div>
</header>

<section class="abs band"></section>
<p class="abs band-text">IF YOU HAVE THE RIGHT TO WORK, Don’t let anyone take it away.</p>
<div class="abs band-btn">EMPLOYMENT APPLICATION FORM</div>

<h2 class="abs section-title" style="top:855px">WELCOME TO <em>TOLVANE INC.</em></h2>
<p class="abs welcome-copy">Tolvane is a third party debt collection agency that is focused on the collection of higher education loans. Tolvane is compliant with all federal, state, and local laws and is committed to the professional and fair treatment of consumers. Our goal is to assist consumers in resolving their obligations in the manner that best meets their needs and to provide information necessary in order for consumers to make an informed decision.</p>

<section class="abs credentials"></section>
<div class="abs badge" style="left:92px;top:1150px;width:120px;height:188px"></div>
<h3 class="abs cred-title" style="left:266px;top:1147px">Member of Meridian Guild</h3>
<p class="abs cred-copy" style="left:266px;top:1184px;width:310px">Lorem Ipsum is simply dummy text of the printing and typesetting industry. Lorem Ipsum has been the industry's standard dummy text ever since the 1500.</p>
<div class="abs divider"></div>
<div class="abs badge" style="left:644px;top:1150px;width:131px;height:188px"></div>
<h3 class="abs cred-title" style="left:809px;top:1147px;width:290px">Accredited by the Fair Trade Council</h3>
<p class="abs cred-copy" style="left:809px;top:1218px;width:320px">Lorem Ipsum is simply dummy text of the printing and typesetting industry. Lorem Ipsum has been the industry's standard dummy text ever since the 1500.</p>

<h2 class="abs section-title" style="top:1438px">FREE <em>ADVICE</em></h2>
<p class="abs advice-copy">Best meets their needs and to provide information necessary in order for consumers to make an informed decision.</p>
<div class="abs call-label">CALL US NOW!</div>
<div class="abs call-icon">
  <svg width="60" height="60" viewBox="0 0 60 60"><path d="M22 19c2-1 4 0 5 2l2 4c1 2 0 3-1 4l-1 1c1 3 3 5 6 6l1-1c1-1 2-2 4-1l4 2c2 1 3 3 2 5l-1 2c-1 2-4 2-6 1-8-3-14-9-17-17-1-2-1-5 1-6z" fill="var(--crimson)"/></svg>
</div>
<div class="abs call-number">123 456 7890</div>

<section class="abs testimonials"></section>
<h2 class="abs section-title" style="top:1729px">WHAT OUR <em>CLIENT SAY</em></h2>
<div class="abs avatar" style="left:77px;top:1807px" role="img" aria-label="Portrait of a smiling woman client"></div>
<p class="abs quote" style="left:220px;top:1811px">Lorem Ipsum is simply dummy text of the printing and typesetting industry. Lorem Ipsum has been the industry's standard dummy text ever since the 1500.</p>
<p class="abs client" style="left:220px;top:1938px">- CLIENT NAME</p>
<div class="abs avatar" style="left:639px;top:1807px" role="img" aria-label="Portrait of a smiling man client in a suit"></div>
<p class="abs quote" style="left:781px;top:1811px">Lorem Ipsum is simply dummy text of the printing and typesetting industry. Lorem Ipsum has been the industry's standard dummy text ever since the 1500.</p>
<p class="abs client" style="left:781px;top:1938px">- CLIENT NAME</p>

<footer class="abs footer"></footer>
<nav class="abs footer-links" style="color:var(--white)"><span>Home</span><span>Consumer</span><span>Career</span><span>Discloser</span></nav>
<div class="abs social" style="left:997px"></div>
<div class="abs social" style="left:1049px"></div>
<div class="abs social" style="left:1101px"></div>
<div class="abs footer-rule"></div>
<div class="abs footer-heading" style="color:var(--white)">Contact us</div>
<svg class="abs" style="left:77px;top:2158px" width="14" height="20" viewBox="0 0 14 20"><path d="M7 0a7 7 0 0 0-7 7c0 5 7 13 7 13s7-8 7-13a7 7 0 0 0-7-7zm0 10a3 3 0 1 1 0-6 3 3 0 0 1 0 6z" fill="var(--white)"/></svg>
<p class="abs footer-item" style="left:102px;top:2152px;width:220px;color:var(--white)">Lorem Ipsum is simply dummy text of the printing.</p>
<svg class="abs" style="left:381px;top:2156px" width="22" height="22" viewBox="0 0 60 60"><path d="M12 9c2-1 4 0 5 2l3 6c1 2 0 3-1 4l-2 2c2 6 6 10 12 12l2-2c1-1 2-2 4-1l6 3c2 1 3 3 2 5l-2 4c-1 2-4 3-6 2C22 41 13 32 8 19c-1-2 0-5 2-6z" fill="var(--white)"/></svg>
<p class="abs" style="left:418px;top:2150px;font-size:20px;font-weight:700;color:var(--white)">123 456 7890</p>
<svg class="abs" style="left:640px;top:2160px" width="21" height="16" viewBox="0 0 21 16"><rect x="1" y="1" width="19" height="14" rx="1.5" fill="none" stroke="var(--white)" stroke-width="1.8"/><path d="M1.5 2l9 7 9-7" fill="none" stroke="var(--white)" stroke-width="1.8"/></svg>
<p class="abs footer-item" style="left:665px;top:2155px;color:var(--white)">info@tolvaneinc.co.uk</p>
<p class="abs footer-item" style="left:951px;top:2149px;color:var(--white)">© Tolvane Inc. - 2016.<br>All Rights Reserved.</p>

</body>
</html>
```